Illustrationen für Familien-, Erziehungsberatung und Jugendberatung
Zielgruppe
Familien-, Erziehungsberatung und Jugendberatung in Frankfurt von 14 Erziehungsberatungsstellen
Zielgruppe: Eltern, Kinder und Jugendliche
Wir beraten bei familiären Krisen, Fragen zur Entwicklung und Erziehung, Beziehungsproblemen etc.
Aufgabenstellung
ansprechende Illustration für Familien (Eltern, Kinder und Jugendliche), diversitäts- und kultursensibel, inklusiv
das Bild oben auf der Flyervorderseite (siehe pdf) soll ersetzt werden, da zu stereotyp

```html
<!DOCTYPE html>
<html lang="de">
<head>
<meta charset="utf-8">
<title>Beratung für Eltern, Kinder und Jugendliche</title>
<link rel="stylesheet" href="https://fonts.googleapis.com/css2?family=Source+Sans+3:wght@600;700&family=Open+Sans:wght@700&display=swap">
<style>
  :root {
    --orange: #f0993a;
    --orange-dark: #e08a2c;
    --green: #b7cc2a;
    --brown: #5b3a14;
    --beige: #ebe3dc;
    --white: #fdfcfb;
  }
  * { margin: 0; padding: 0; box-sizing: border-box; }
  html, body { width: 1200px; height: 2533px; overflow: hidden; background: var(--white); }
  .flyer { position: relative; width: 1200px; height: 2533px; background: var(--white); font-family: "Source Sans 3", sans-serif; }
  .top-bar { position: absolute; left: 0; top: 0; width: 1200px; height: 24px; background: var(--orange); }
  .hero-illustration { position: absolute; left: 0; top: 24px; width: 1200px; height: 867px; }
  .hero-rule { position: absolute; left: 0; top: 889px; width: 1200px; height: 4px; background: var(--orange); }
  .green-band { position: absolute; left: 0; top: 909px; width: 1200px; height: 24px; background: var(--green); }
  .count-badge { position: absolute; left: 624px; top: 840px; width: 574px; height: 574px; }
  .count-badge__text { position: absolute; left: 624px; top: 880px; width: 574px; text-align: center; color: #fff; }
  .count-badge__number { font-size: 124px; font-weight: 700; line-height: 1.1; }
  .count-badge__label { font-size: 52px; font-weight: 600; line-height: 68px; margin-top: 4px; }
  .headline { position: absolute; left: 113px; top: 1108px; font-size: 78px; font-weight: 700; line-height: 100px; color: var(--brown); }
  .subline { position: absolute; left: 113px; top: 1502px; font-size: 68px; font-weight: 600; line-height: 100px; color: var(--orange); }
  .info-label { position: absolute; left: 113px; top: 1804px; font-size: 46px; font-weight: 700; color: var(--brown); }
  .url-band { position: absolute; left: 0; top: 1887px; width: 1200px; height: 160px; background: var(--orange); display: flex; align-items: center; justify-content: center; }
  .url-band__text { font-family: "Open Sans", sans-serif; font-size: 88px; font-weight: 700; color: #fff; letter-spacing: 2px; }
  .org-mark { position: absolute; left: 100px; top: 2190px; display: flex; align-items: center; gap: 40px; }
  .org-mark__square { width: 130px; height: 130px; background: var(--orange); opacity: 0.8; }
  .org-mark__name { font-size: 50px; font-weight: 700; line-height: 54px; color: var(--orange); }
  .bottom-band { position: absolute; left: 0; top: 2480px; width: 1200px; height: 53px; background: var(--green); }
</style>
</head>
<body>
<main class="flyer">
  <div class="top-bar"></div>

  <svg class="hero-illustration" viewBox="0 0 1200 867" role="img" aria-label="Illustration: vielfältige Familien, Eltern, Kinder und Jugendliche vor der Skyline von Frankfurt am Main">
    <defs>
      <linearGradient id="heroFill" x1="0" y1="0" x2="0" y2="1">
        <stop offset="0" stop-color="#e9e2dc"/>
        <stop offset="0.45" stop-color="#b9b3b4"/>
        <stop offset="1" stop-color="#e8dfd6"/>
      </linearGradient>
    </defs>
    <rect width="1200" height="867" fill="url(#heroFill)"/>
    <path d="M0 867 L0 640 Q60 820 230 867 Z" fill="#ffffff"/>
  </svg>
  <div class="hero-rule"></div>
  <div class="green-band"></div>

  <svg class="count-badge" viewBox="0 0 574 574" aria-hidden="true">
    <circle cx="287" cy="287" r="287" fill="#ffffff"/>
    <circle cx="287" cy="287" r="272" fill="var(--orange)"/>
    <circle cx="287" cy="287" r="258" fill="var(--orange-dark)" opacity="0.35"/>
  </svg>
  <div class="count-badge__text">
    <div class="count-badge__number">14</div>
    <div class="count-badge__label">Erziehungs- und<br>Familienberatungs-<br>stellen in Frankfurt<br>am Main</div>
  </div>

  <h1 class="headline">Beratung für<br>Eltern, Kinder<br>und Jugendliche</h1>
  <p class="subline">durch pädagogische und<br>psychologische Fachkräfte</p>
  <p class="info-label">Für nähere Informationen:</p>

  <div class="url-band"><span class="url-band__text">www.familienrat-main.de</span></div>

  <div class="org-mark">
    <div class="org-mark__square"></div>
    <div class="org-mark__name">Beratungsverbund<br>Mainbogen</div>
  </div>

  <div class="bottom-band"></div>
</main>
</body>
</html>
```